Menu Design Project

Menu design for a Japanese fast food restaurant featuring Teppanyaki and Sushi. The restaurant main scene color is black and wood color. No Japan scenery pictures. Menu try to be simply and elegant . Pictures provided can be used accordingly to the menu items, but doesn't have to be due to the back ground color of the picture is white.

Target Market(s)

Young and progressive consumers

Industry/Entity Type

Asian Restaurant

Font styles to use
Other font styles liked:
• Han Wang Kan Tan Font

Colors
1b1b1b
fee18a

Requirements
Must have
• Pictures of the Sushi that is provided, and all the item in the Word file.
Nice to have
• Keep it simple but different
Should not have
• No scenery pictures, no cherry blossom.

```html
<!DOCTYPE html>
<html lang="en">
<head>
<meta charset="utf-8">
<title>Sushi Menu</title>
<link rel="stylesheet" href="https://fonts.googleapis.com/css2?family=Anton&family=Roboto+Condensed:wght@400;500;700&display=swap">
<style>
:root{
  --ink:#1b1b1b;
  --gold:#fee18a;
  --gold-deep:#f6d56a;
  --paper:#ffffff;
  --text:#1b1b1b;
  --soft:#333;
}
*{margin:0;padding:0;box-sizing:border-box}
html,body{width:1200px;height:928px;overflow:hidden;background:var(--gold)}
body{font-family:"Roboto Condensed",Arial,sans-serif;color:var(--text)}
.menu{position:relative;width:1200px;height:928px;overflow:hidden}
.backdrop{position:absolute;inset:0}
.bar{position:absolute;background:var(--ink);color:var(--gold);font-family:"Anton",Impact,sans-serif;
  font-size:33px;line-height:1;text-align:center;display:flex;align-items:center;justify-content:center;letter-spacing:.5px}
.bar.two-line{flex-direction:column;font-size:33px;line-height:1.02}
.item{position:absolute}
.name{font-weight:500;font-size:15.5px;line-height:1.15;text-transform:uppercase}
.name small{font-size:13px;text-transform:none;font-weight:400}
.desc{font-size:13px;line-height:1.25;color:var(--soft)}
.price{position:absolute;font-weight:700;font-size:13px}
.sizes{position:absolute;font-weight:700;font-size:11.5px;line-height:1.55;text-align:left}
.photo{position:absolute;border-radius:10px}
.thumb{position:absolute;width:52px;height:30px;border-radius:6px;background:linear-gradient(135deg,#f3a76b,#e9e2cf 60%,#7bb168)}
.note{position:absolute;left:805px;top:583px;width:395px;height:61px;background:var(--gold);text-align:center;padding-top:12px}
.note b{display:block;font-size:14.5px;font-weight:500}
.note span{display:block;font-size:11.5px;line-height:1.1}
.block-text{position:absolute;font-size:13px;line-height:1.25}
.block-text .label{font-size:15.5px;font-weight:500;text-transform:uppercase;display:block}
.hand-price{position:absolute;left:318px;top:812px;font-size:13px;line-height:1.25;white-space:nowrap}
</style>
</head>
<body>
<div class="menu">
  <svg class="backdrop" width="1200" height="928" viewBox="0 0 1200 928" aria-hidden="true">
    <defs>
      <radialGradient id="burst" cx="50%" cy="50%" r="60%">
        <stop offset="0" stop-color="#ffffff"/>
        <stop offset="1" stop-color="#e9e9e9"/>
      </radialGradient>
    </defs>
    <rect width="1200" height="928" fill="#fde68f"/>
    <polygon points="0,50 405,28 830,22 850,130 1200,140 1200,650 900,700 835,928 380,915 0,875" fill="url(#burst)"/>
  </svg>

  <div class="bar" style="left:0;top:53px;width:402px;height:43px">APPETIZER</div>
  <div class="item" style="left:27px;top:102px"><div class="name">Seaweed Salad</div><div class="desc">seasoned seaweed</div></div>
  <div class="price" style="left:354px;top:120px">$2.99</div>
  <div class="item" style="left:27px;top:138px"><div class="name">Kani Salad Spicy or Non-Spicy</div><div class="desc">crab meat, cucumber, lettuce with dressing</div></div>
  <div class="price" style="left:354px;top:155px">$3.99</div>
  <div class="item" style="left:27px;top:193px"><div class="name">Tempura Shrimp</div><div class="desc">4 Pieces Fried Tempura Shrimp</div></div>
  <div class="price" style="left:354px;top:210px">$5.99</div>
  <div class="photo" role="img" aria-label="Fried tempura shrimp" style="left:242px;top:178px;width:90px;height:82px;background:radial-gradient(circle,#f7d94a,#f2c230 60%,transparent 72%)"></div>
  <div class="item" style="left:27px;top:268px"><div class="name">Fried Gyoza <small>(6pcs)</small></div></div>
  <div class="price" style="left:354px;top:270px">$3.99</div>
  <div class="item" style="left:27px;top:288px"><div class="name">Spring Roll <small>(4pcs)</small></div></div>
  <div class="price" style="left:354px;top:290px">$2.59</div>
  <div class="item" style="left:27px;top:310px"><div class="name">Crab Rangoon <small>(5pcs)</small></div></div>
  <div class="price" style="left:354px;top:312px">$4.50</div>

  <div class="bar" style="left:0;top:340px;width:402px;height:43px">SASHIMI</div>
  <div class="block-text" style="left:27px;top:400px">*Salmon, *Tuna, *Yellow Tail,<br>*Red Snapper, *White Tuna,<br>Surf Clam</div>
  <div class="photo" role="img" aria-label="Sashimi rosettes" style="left:202px;top:390px;width:200px;height:55px;background:linear-gradient(90deg,#f6a676,#e8546a 35%,#f2b4a4 65%,#f3e3b2)"></div>

  <div class="bar" style="left:0;top:462px;width:402px;height:43px">SUSHI NIGIRI</div>
  <div class="block-text" style="left:27px;top:516px">*Salmon, *Tuna, *Yellow Tail,<br>*Red Snapper, *White Tuna,<br>Surf Clam, Grill Eel, Ebi Shrimp,<br>Kani crab meat</div>
  <div class="photo" role="img" aria-label="Salmon nigiri" style="left:263px;top:508px;width:98px;height:52px;background:linear-gradient(160deg,#f79a62,#fbc9a4 55%,#f4f1ea)"></div>
  <div class="block-text" style="left:264px;top:561px">5 pieces for <b>$5.99</b></div>

  <div class="bar two-line" style="left:0;top:587px;width:402px;height:72px"><span>HAND ROLL BUILD YOUR</span><span>OWN:</span></div>
  <div class="block-text" style="left:27px;top:669px">
    <span class="label">Pick One Protein:</span>*Salmon, *Tuna, *Yellow Tail, *Red Snapper,<br>*White Tuna, Surf Clam, Grill Eel, Ebi Shrimp,<br>Kani crab meat
    <span class="label">Pick Two Vegetable:</span>Cucumber, Avocado, Lettuce, Oshigo,<br>Asparagus, Seaweed
    <span class="label">Pick Sauce:</span>Spicy Mayonnaise, Honey Wasabi,<br>Honey Mayonnaise, Unagi Sauce
  </div>
  <div class="photo" role="img" aria-label="Seaweed hand roll cone" style="left:308px;top:672px;width:78px;height:128px;background:linear-gradient(180deg,#7a9c3c,#2f3a2a 35%,#1f2620)"></div>
  <div class="hand-price">2 for<b>$5.99</b></div>

  <div class="bar" style="left:403px;top:30px;width:402px;height:44px">SUSHI</div>
  <div class="block-text" style="left:403px;top:84px;width:432px;text-align:center;font-size:14.5px">Ingredients subject to availability</div>
  <div class="item" style="left:485px;top:101px;font-size:21px;font-weight:700">SPECIAL ROLL</div>

  <div class="thumb" role="img" aria-label="Dragon roll" style="left:413px;top:132px"></div>
  <div class="item" style="left:485px;top:126px"><div class="name">Dragon Roll</div><div class="desc">Grilled Eel fish &amp; cucumber top with<br>avocado &amp; Unagi sauce</div></div>
  <div class="price" style="left:757px;top:161px">$9.99</div>
  <div class="item" style="left:485px;top:178px"><div class="name">Deluxe Black Dragon Roll</div><div class="desc">Tempura Shrimp top with Avocado,<br>Grilled Eel fish &amp; Unagi sacue</div></div>
  <div class="price" style="left:757px;top:213px">$11.99</div>
  <div class="thumb" role="img" aria-label="Rainbow roll" style="left:413px;top:237px"></div>
  <div class="item" style="left:485px;top:231px"><div class="name">*Rainbow Roll</div><div class="desc">avocado, cucumber &amp; Kani top with red<br>snapper, tuna, salmon&amp;avocado</div></div>
  <div class="price" style="left:757px;top:266px">$10.99</div>
  <div class="thumb" role="img" aria-label="Four season roll" style="left:413px;top:290px"></div>
  <div class="item" style="left:485px;top:284px"><div class="name">*Four Season Roll</div><div class="desc">Tuna, salmon, oshinko</div></div>
  <div class="price" style="left:757px;top:303px">$9.99</div>
  <div class="item" style="left:485px;top:321px"><div class="name">*Deluxe Philly Roll</div><div class="desc">Salmon, cream cheese &amp; avocado top<br>with more salmon</div></div>
  <div class="price" style="left:757px;top:356px">$9.9</div>
  <div class="thumb" role="img" aria-label="Massago roll" style="left:413px;top:378px"></div>
  <div class="item" style="left:485px;top:373px"><div class="name">*Massago Roll</div><div class="desc">Kani crab meat, cucumber &amp; avocado top<br>with Premium Massago Roe</div></div>
  <div class="price" style="left:757px;top:408px">$8.99</div>
  <div class="thumb" role="img" aria-label="Deluxe spicy tuna roll" style="left:413px;top:430px"></div>
  <div class="item" style="left:485px;top:426px"><div class="name">*Deluxe Spicy Tuna Roll</div><div class="desc">Kani crab meat, Cucumber &amp; avocado top<br>with Spicy grounded tuna</div></div>
  <div class="price" style="left:757px;top:461px">$9.49</div>
  <div class="thumb" role="img" aria-label="Deluxe spicy kani roll" style="left:413px;top:482px"></div>
  <div class="item" style="left:485px;top:478px"><div class="name">Deluxe Spicy Kani Roll</div><div class="desc">Kani crab meat, cucumber &amp; avocado top<br>with seasoned ground Crab meat</div></div>
  <div class="price" style="left:757px;top:513px">$9.49</div>
  <div class="thumb" role="img" aria-label="Deluxe kani roll" style="left:413px;top:535px"></div>
  <div class="item" style="left:485px;top:531px"><div class="name">Deluxe Kani Roll</div><div class="desc">Kani crab meat, cucumber &amp; avocado top<br>with Kani &amp; Panko crumb</div></div>
  <div class="price" style="left:757px;top:566px">$9.49</div>
  <div class="thumb" role="img" aria-label="Tri deluxe fish roll" style="left:426px;top:585px;width:30px;height:36px;border-radius:50%"></div>
  <div class="item" style="left:485px;top:584px"><div class="name">*Tri Deluxe Fish Roll</div><div class="desc">Tuna, salmon &amp; red snapper</div></div>
  <div class="price" style="left:757px;top:603px">$9.99</div>
  <div class="item" style="left:485px;top:620px"><div class="name">*Sumo Roll</div><div class="desc">Tuna, Salmon, White Tuan, Red snapper<br>Avocado &amp; Kani Crab Meat</div></div>
  <div class="price" style="left:757px;top:655px">$10.99</div>
  <div class="item" style="left:485px;top:673px"><div class="name">*Hamachi Asparagus Roll</div><div class="desc">Hamachi, Scallion &amp; Asparagus with Ponzu<br>Sauce</div></div>
  <div class="price" style="left:757px;top:708px">$7.99</div>

  <div class="bar" style="left:403px;top:726px;width:402px;height:44px">REGULAR MAKI ROLL</div>
  <div class="item" style="left:420px;top:780px"><div class="name">*Salmon Roll</div><div class="desc">salmon &amp; avocado</div></div>
  <div class="sizes" style="left:692px;top:782px">(8pcs) $5.49<br>(12pcs) $7.49</div>
  <div class="item" style="left:420px;top:819px"><div class="name">*Tuna Roll</div><div class="desc">tuna &amp; avocado</div></div>
  <div class="sizes" style="left:692px;top:821px">(8pcs) $5.49<br>(12pcs) $7.49</div>
  <div class="item" style="left:420px;top:859px"><div class="name">*Philly Roll</div><div class="desc">salmon, cream cheese &amp; avocado</div></div>
  <div class="sizes" style="left:692px;top:861px">(8pcs) $5.49<br>(12pcs) $7.49</div>

  <div class="photo" role="img" aria-label="Tuna, snapper and salmon nigiri" style="left:825px;top:30px;width:360px;height:82px;border-radius:40px;background:linear-gradient(90deg,#e23a52,#f7c8c0 40%,#fbd6c2 60%,#f88a54)"></div>
  <div class="item" style="left:810px;top:157px"><div class="name">California Roll</div><div class="desc">cucumber, avocado &amp; kani crab meat</div></div>
  <div class="sizes" style="left:1084px;top:159px">(8pcs) $5.49<br>(12pcs) $7.49</div>
  <div class="item" style="left:810px;top:200px"><div class="name">Kani &amp; Cheese Roll</div><div class="desc">Kani crab meat &amp; cream cheese</div></div>
  <div class="sizes" style="left:1084px;top:202px">(8pcs) $5.49<br>(12pcs) $7.49</div>
  <div class="item" style="left:810px;top:245px"><div class="name">Shrimp Tempura Roll</div><div class="desc">Fried tempura shrimp &amp; cucumber</div></div>
  <div class="sizes" style="left:1084px;top:264px">(8pcs) $6.49</div>
  <div class="thumb" role="img" aria-label="Alaska roll" style="left:1020px;top:274px;width:46px;height:54px"></div>
  <div class="item" style="left:810px;top:291px"><div class="name">*Alaska Roll</div><div class="desc">Salmon &amp; avocado with massago</div></div>
  <div class="sizes" style="left:1084px;top:293px">(8pcs) $5.49<br>(12pcs) $7.49</div>
  <div class="item" style="left:810px;top:336px"><div class="name">Grilled Eel Roll</div><div class="desc">Eel &amp; avocado</div></div>
  <div class="sizes" style="left:1084px;top:338px">(8pcs) $5.49<br>(12pcs) $7.49</div>
  <div class="item" style="left:810px;top:381px"><div class="name">*Spicy Tuna Roll</div><div class="desc">seasoned ground tuna</div></div>
  <div class="sizes" style="left:1084px;top:383px">(8pcs) $5.49<br>(12pcs) $7.49</div>
  <div class="item" style="left:810px;top:427px"><div class="name">*Spicy Salmon Roll</div><div class="desc">seasoned ground salmon</div></div>
  <div class="sizes" style="left:1084px;top:429px">(8pcs) $5.49<br>(12pcs) $7.49</div>
  <div class="item" style="left:810px;top:472px"><div class="name">Spicy Kani Roll</div><div class="desc">seasoned ground crab meat</div></div>
  <div class="sizes" style="left:1084px;top:474px">(8pcs) $5.49<br>(12pcs) $7.49</div>
  <div class="item" style="left:810px;top:517px"><div class="name">Vegetarian Roll</div><div class="desc">avocado, cucumber<br>Add Ajitsuke seasoned fried bean curd</div></div>
  <div class="sizes" style="left:1084px;top:519px">(8pcs) $4.49<br>(16pcs) $7.99<br>for $1.00 more</div>

  <div class="note"><b>*ITEMS MAY BE SERVED RAW OR UNDER COOKED</b><span>consuming raw or undercooked meat, poultry, shellfish, eggs<br>or seafood may increase your risk of food borne illness.</span></div>

  <div class="photo" role="img" aria-label="Close-up of a salmon, cream cheese and avocado roll" style="left:900px;top:668px;width:208px;height:215px;border-radius:38%;background:linear-gradient(135deg,#f6f3ea,#ece6d6)"></div>
</div>
</body>
</html>
```